Web Developer Needs a Business Card Design

I need a personal business card design that represents me as a web developer for potential employers. I would like the background to be a dark color on the front for contrast with my logo and name. The back will have all my information along with a smaller version of the logo. I want something with a modern look and feel, not too conservative. This will be used for potential employers and freelance work.

Industry/Entity Type

Business

Contact Information for Business Card

Front should have my logo and name. The back should have all my personal information which would include: name: Tom Varulek, phone: 570-614-3098, email: tomvarulek@quillbox.net, website url: www.tomvarulek.net, logo, web developer.

Font styles to use
Sans Serif

Requirements
Must have
• Must include my logo. The color palette base color will be the logo color.

```html
<!DOCTYPE html>
<html lang="en">
<head>
<meta charset="utf-8">
<title>Tom Varulek – Business Card</title>
<link rel="stylesheet" href="https://fonts.googleapis.com/css2?family=Open+Sans:wght@400;600&display=swap">
<style>
  :root {
    --bg: #e9e6e1;
    --card-dark: #231d1b;
    --card-light: #ffffff;
    --mint: #5fd4b8;
    --mint-soft: #9fe3d2;
    --text-light: #f4f4f4;
    --photo-a: #eef1f4;
    --photo-b: #8cc6ec;
  }
  * { margin: 0; padding: 0; box-sizing: border-box; }
  html, body { width: 1200px; height: 892px; overflow: hidden; }
  body {
    background: var(--bg);
    font-family: "Open Sans", sans-serif;
    position: relative;
  }
  .card {
    position: absolute;
    width: 600px;
    height: 343px;
    border-radius: 4px;
    overflow: hidden;
    box-shadow: 0 6px 18px rgba(0,0,0,.18);
  }
  /* Front */
  .card-front { left: 60px; top: 60px; background: var(--card-dark); }
  .card-front .mark {
    position: absolute; left: 210px; top: 40px;
    width: 180px; height: 180px; border-radius: 50%;
    border: 12px solid var(--mint);
    display: flex; align-items: center; justify-content: center;
    color: var(--mint); font-weight: 600; font-size: 22px; text-align: center; line-height: 1.15;
  }
  .card-front .name {
    position: absolute; left: 0; right: 0; top: 246px;
    text-align: center; color: var(--mint);
    font-size: 44px; font-weight: 400; letter-spacing: .5px;
  }
  /* Back */
  .card-back { left: 540px; top: 489px; background: var(--card-light); }
  .card-back .shape { position: absolute; inset: 0; }
  .card-back .photo {
    position: absolute; left: 28px; top: 40px; width: 190px; height: 150px;
    border-radius: 6px;
    background: radial-gradient(circle at 70% 45%, var(--photo-b), var(--photo-a) 70%);
  }
  .card-back .mark {
    position: absolute; right: 30px; top: 28px;
    width: 108px; height: 108px; border-radius: 50%;
    border: 7px solid var(--mint);
    display: flex; align-items: center; justify-content: center;
    color: var(--mint); font-weight: 600; font-size: 14px; text-align: center; line-height: 1.15;
  }
  .card-back .info {
    position: absolute; right: 30px; top: 150px; text-align: right;
  }
  .info .name { color: var(--mint); font-size: 34px; font-weight: 400; line-height: 1.05; }
  .info .role { color: var(--text-light); font-size: 19px; margin-bottom: 18px; }
  .contact-list { list-style: none; }
  .contact-list li {
    color: var(--text-light); font-size: 17px; line-height: 1.45;
    display: flex; justify-content: flex-end; align-items: center; gap: 10px;
  }
  .contact-list svg { width: 16px; height: 16px; flex: none; }
</style>
</head>
<body>

  <section class="card card-front" aria-label="Card front">
    <div class="mark">Tom<br>Varulek</div>
    <div class="name">Tom Varulek</div>
  </section>

  <section class="card card-back" aria-label="Card back">
    <svg class="shape" width="600" height="343" viewBox="0 0 600 343" aria-hidden="true">
      <path d="M240 0 Q300 180 270 343 L600 343 L600 0 Z" fill="var(--card-dark)"/>
      <path d="M240 0 Q300 180 270 343" fill="none" stroke="var(--mint-soft)" stroke-width="10"/>
    </svg>
    <div class="photo" role="img" aria-label="Photo of an open laptop with a blue globe emerging from the screen"></div>
    <div class="mark">Tom<br>Varulek</div>
    <div class="info">
      <div class="name">Tom Varulek</div>
      <div class="role">web developer</div>
      <ul class="contact-list">
        <li>570-614-3098
          <svg viewBox="0 0 16 16"><rect width="16" height="16" rx="2" fill="var(--mint)"/><path d="M5 3.5l2 2-1 1.2c.6 1.4 1.5 2.3 2.9 2.9l1.2-1 2 2-1.3 1.5C7.3 11.8 4.2 8.7 3.5 4.8z" fill="var(--card-dark)"/></svg>
        </li>
        <li>www.tomvarulek.net
          <svg viewBox="0 0 16 16"><rect width="16" height="16" rx="2" fill="var(--mint)"/><circle cx="8" cy="8" r="4.8" fill="none" stroke="var(--card-dark)" stroke-width="1.3"/><path d="M3.2 8h9.6M8 3.2c-2 2.8-2 6.8 0 9.6M8 3.2c2 2.8 2 6.8 0 9.6" fill="none" stroke="var(--card-dark)" stroke-width="1"/></svg>
        </li>
        <li>tomvarulek@quillbox.net
          <svg viewBox="0 0 16 16"><rect width="16" height="16" rx="2" fill="var(--mint)"/><rect x="3" y="4.5" width="10" height="7" fill="none" stroke="var(--card-dark)" stroke-width="1.3"/><path d="M3 4.5l5 4 5-4" fill="none" stroke="var(--card-dark)" stroke-width="1.3"/></svg>
        </li>
      </ul>
    </div>
  </section>

</body>
</html>
```